KAJU Freightways #ALLKAJU Business Cards & Letterhead

I am looking to business cards designed for our organization. We are currently undergoing a small re-branding that is taking place. Our organization is called KAJU Freightways and we are headquartered in Phoenix, AZ. We primarily provide transportation and logistics services to the Marlow Parcel Bureau who is our largest customer. I would like to see a design that incorporates name, title, contact info, website, and address (this will be different depending on the employee). I would also like to see some color on the business card using our logo colors or a variation. I would like our logo on the back of the business card with the website displayed. The final design should communicate that we are a next generation transportation operate that focuses on being driver-first, customer-centric, innovative, and sustainable.We would also like our #ALLKAJU catch phrase incorporated as well.

Target Market(s)

Transportation & Logistics

Industry/Entity Type

Trucking Company

Contact Information for Business Card

-First and Last Name
-Position Title
-Contact Phone
-Contact Email
-Physical Address

Font styles to use
Serif

Colors

Designer to choose colors to be used in the design.

Requirements
Must have
• -KAJU logo prominently displayed
• -#ALLKAJU catch phrase used
• -Some amount of color, design gradient, etc.
• -Logo on the back with website listed (https://www.kajufreightco.example)

```html
<!DOCTYPE html>
<html lang="en">
<head>
<meta charset="utf-8">
<title>KAJU Freightways Business Card</title>
<link href="https://fonts.googleapis.com/css2?family=Lora:wght@400;700&display=swap" rel="stylesheet">
<style>
  :root {
    --teal: #033a47;
    --green: #7dc242;
    --white: #ffffff;
    --ink: #0d2f38;
    --backdrop: #2a2a2c;
  }
  * { margin: 0; padding: 0; box-sizing: border-box; }
  html, body {
    width: 1200px;
    height: 1200px;
    overflow: hidden;
    background: var(--backdrop);
    font-family: "Lora", serif;
  }
  .sheet {
    width: 1200px;
    height: 1200px;
    display: flex;
    flex-direction: column;
    align-items: center;
    justify-content: center;
    gap: 56px;
  }
  .card {
    position: relative;
    width: 900px;
    height: 514px;
    overflow: hidden;
  }
  .brand-name {
    display: flex;
    align-items: center;
    gap: 16px;
    font-weight: 700;
    letter-spacing: 2px;
    line-height: 1;
  }
  .brand-dot {
    flex: none;
    border-radius: 50%;
    background: var(--green);
  }
  /* Back side */
  .card-back { background: var(--teal); }
  .back-brand {
    position: absolute;
    left: 0;
    right: 0;
    top: 170px;
    justify-content: center;
    color: var(--white);
    font-size: 96px;
  }
  .back-brand .brand-dot { width: 30px; height: 30px; }
  .back-url {
    position: absolute;
    left: 0;
    right: 0;
    top: 396px;
    text-align: center;
    color: var(--white);
    font-size: 21px;
    letter-spacing: 6px;
  }
  .back-tag {
    position: absolute;
    left: 0;
    right: 0;
    top: 440px;
    text-align: center;
    color: var(--green);
    font-size: 20px;
    font-weight: 700;
    letter-spacing: 3px;
  }
  /* Front side */
  .card-front { background: var(--white); }
  .front-art {
    position: absolute;
    inset: 0;
  }
  .front-brand {
    position: absolute;
    left: 488px;
    top: 101px;
    width: 344px;
    height: 344px;
    justify-content: center;
    color: var(--teal);
    font-size: 84px;
  }
  .front-brand .brand-dot { width: 26px; height: 26px; }
  .details {
    position: absolute;
    left: 52px;
    top: 50px;
    color: var(--ink);
  }
  .company {
    font-weight: 700;
    font-size: 36px;
    color: var(--teal);
    white-space: nowrap;
  }
  .company .accent { color: var(--green); }
  .person-name {
    margin-top: 24px;
    font-weight: 700;
    font-size: 30px;
    color: var(--teal);
    line-height: 1;
  }
  .person-title {
    font-size: 23px;
    color: var(--green);
    line-height: 1.2;
  }
  .address {
    margin-top: 20px;
    font-size: 20px;
    line-height: 1.3;
  }
  .contacts {
    margin-top: 18px;
    list-style: none;
    font-size: 21px;
    line-height: 1.6;
  }
  .contacts li {
    display: flex;
    align-items: center;
    gap: 10px;
  }
  .contacts svg { width: 24px; height: 24px; flex: none; }
  .contacts .accent { color: var(--green); font-weight: 700; }
</style>
</head>
<body>
<main class="sheet">

  <section class="card card-back" aria-label="Business card back">
    <div class="brand-name back-brand">
      <span class="brand-dot"></span>
      <span>KAJU</span>
    </div>
    <p class="back-url">www.kajufreightco.example</p>
    <p class="back-tag">#ALLKAJU</p>
  </section>

  <section class="card card-front" aria-label="Business card front">
    <svg class="front-art" viewBox="0 0 900 514" aria-hidden="true">
      <rect x="690" y="0" width="210" height="514" fill="var(--teal)"/>
      <circle cx="660" cy="273" r="198" fill="var(--white)"/>
    </svg>
    <div class="brand-name front-brand">
      <span class="brand-dot"></span>
      <span>KAJU</span>
    </div>

    <div class="details">
      <h1 class="company">KAJU <span class="accent">Freightways</span></h1>
      <h2 class="person-name">Dorian Vell</h2>
      <p class="person-title">Director</p>
      <p class="address">4120 North Saguaro Bend Road<br>Phoenix, AZ 85019</p>
      <ul class="contacts">
        <li>
          <svg viewBox="0 0 24 24"><circle cx="12" cy="12" r="10.5" fill="none" stroke="var(--green)" stroke-width="1.6"/><path d="M9 7.2c.6-.4 1.2-.3 1.5.3l.8 1.7c.2.5 0 1-.4 1.3l-.6.4c.5 1.3 1.4 2.4 2.6 3.1l.5-.6c.4-.4.9-.5 1.4-.2l1.6 1c.5.3.6 1 .2 1.5-.9 1-2.2 1.2-3.4.6-2.6-1.3-4.5-3.6-5.2-6.4-.3-1.1.1-2.1 1-2.7z" fill="var(--green)"/></svg>
          <span>602-555-0148</span>
        </li>
        <li>
          <svg viewBox="0 0 24 24"><circle cx="12" cy="12" r="10.5" fill="none" stroke="var(--green)" stroke-width="1.6"/><rect x="6.5" y="8" width="11" height="8" rx="1" fill="var(--green)"/><path d="M6.8 8.4 12 12.6l5.2-4.2" fill="none" stroke="var(--white)" stroke-width="1.2"/></svg>
          <span>info@kajufreightco.example</span>
        </li>
        <li>
          <svg viewBox="0 0 24 24"><circle cx="12" cy="12" r="10.5" fill="none" stroke="var(--green)" stroke-width="1.6"/><circle cx="12" cy="12" r="6.5" fill="none" stroke="var(--green)" stroke-width="1.3"/><ellipse cx="12" cy="12" rx="3" ry="6.5" fill="none" stroke="var(--green)" stroke-width="1.1"/><path d="M5.5 12h13M6.5 9h11M6.5 15h11" stroke="var(--green)" stroke-width="1"/></svg>
          <span>www.<span class="accent">kajufreightco</span>.example</span>
        </li>
      </ul>
    </div>
  </section>

</main>
</body>
</html>
```